Need help in designing new business card utilizing our new logo.

BuildMark Solutions works with Construction Business Owners, Managers & IT Professionals to strengthen software usage and increase user productivity.

Our Construction Accounting and Mobile Field Management Software Clients engage with us in the following areas:

New Software Implementations
Software Re-Implementations
Redesigning Software Usage at the User Level
Project Coordination & Management
Continued Software Support

Old tag line:
Weighing Options - Implementing Solutions

www.buildmark-solutions.example

Ridge 4 is a product, but not needed for a new business card.

```html
<!DOCTYPE html>
<html lang="en">
<head>
<meta charset="utf-8">
<title>BuildMark Solutions – Business Card</title>
<link rel="stylesheet" href="https://fonts.googleapis.com/css2?family=Open+Sans:wght@400;600;700&display=swap">
<style>
  :root {
    --brand-blue: #2b3494;
    --swoosh-grey: #bfc0c3;
    --card-white: #ffffff;
    --map-grey: #eceded;
    --ink: #2e2e2e;
    --stage: #3a3a3a;
  }
  * { margin: 0; padding: 0; box-sizing: border-box; }
  html, body { width: 1200px; height: 800px; overflow: hidden; }
  body {
    background: var(--stage);
    font-family: "Open Sans", Arial, sans-serif;
    position: relative;
  }
  .card {
    position: absolute;
    width: 560px;
    height: 320px;
    background: var(--card-white);
    overflow: hidden;
    box-shadow: 0 10px 24px rgba(0,0,0,.45);
  }
  .card svg.card-art { position: absolute; inset: 0; width: 100%; height: 100%; }
  .card--front { left: 110px; top: 70px; }
  .card--back { left: 520px; top: 410px; }

  .world-map {
    position: absolute;
    left: 150px; top: 20px;
    width: 390px; height: 230px;
    border-radius: 50%;
    background: radial-gradient(ellipse at center, var(--map-grey) 0%, rgba(236,237,237,.6) 55%, rgba(255,255,255,0) 75%);
  }
  .brand {
    position: absolute;
    left: 205px; top: 105px;
    display: flex; align-items: center; gap: 12px;
  }
  .brand__square { width: 34px; height: 34px; background: var(--brand-blue); }
  .brand__name {
    color: var(--brand-blue);
    font-weight: 600;
    font-size: 30px;
    letter-spacing: .5px;
  }

  .contact {
    position: absolute;
    left: 48px; top: 112px;
    color: var(--ink);
  }
  .contact__name { font-size: 26px; font-weight: 700; letter-spacing: .5px; line-height: 1; }
  .contact__role { font-size: 14px; font-weight: 700; margin-top: 2px; }
  .contact__address { font-size: 13px; line-height: 1.35; margin-top: 20px; }
  .contact__list { list-style: none; margin-top: 14px; font-size: 13px; line-height: 1.4; }
  .contact__list li { display: flex; align-items: center; gap: 9px; }
  .contact__list svg { width: 12px; height: 12px; fill: var(--brand-blue); flex: none; }
  .contact__domain { color: var(--brand-blue); font-weight: 600; }
</style>
</head>
<body>

  <section class="card card--front" aria-label="Card front">
    <svg class="card-art" viewBox="0 0 560 320" preserveAspectRatio="none" aria-hidden="true">
      <rect width="560" height="320" fill="var(--brand-blue)"/>
      <path d="M60,0 C-15,130 110,265 330,320 L560,320 L560,0 Z" fill="var(--card-white)"/>
      <path d="M68,0 C-2,130 120,262 330,320 L560,320 L560,0 Z" fill="var(--swoosh-grey)"/>
      <path d="M105,0 C45,130 155,255 330,320 L560,320 L560,0 Z" fill="var(--card-white)"/>
    </svg>
    <div class="world-map" role="img" aria-label="Faint world map in the background"></div>
    <div class="brand">
      <span class="brand__square"></span>
      <span class="brand__name">BuildMark Solutions</span>
    </div>
  </section>

  <section class="card card--back" aria-label="Card back">
    <svg class="card-art" viewBox="0 0 560 320" preserveAspectRatio="none" aria-hidden="true">
      <rect width="560" height="320" fill="var(--brand-blue)"/>
      <path d="M0,0 L430,0 C600,60 590,210 300,320 L0,320 Z" fill="var(--swoosh-grey)"/>
      <path d="M0,0 L360,0 C560,50 580,200 300,320 L0,320 Z" fill="var(--card-white)"/>
      <path d="M455,85 C525,170 470,255 332,320 L310,320 C450,248 502,170 455,85 Z" fill="var(--brand-blue)"/>
    </svg>
    <div class="contact">
      <h1 class="contact__name">DANA R. WHITFIELD</h1>
      <p class="contact__role">Owner</p>
      <p class="contact__address">14 Harbor Lane - Suite 210<br>Millbrook NY 12545</p>
      <ul class="contact__list">
        <li><svg viewBox="0 0 12 12"><path d="M2.5 0.5 L4.5 2.8 L3.4 4.3 C4.2 6 5.7 7.6 7.6 8.6 L9 7.5 L11.5 9.5 L10 11.5 C5 11 1 7 0.5 2 Z"/></svg>800-555-0142 ext.100</li>
        <li><svg viewBox="0 0 12 12"><path d="M3 0 H9 V12 H3 Z M4 1.5 V9 H8 V1.5 Z"/></svg>518-555-0187</li>
        <li><svg viewBox="0 0 12 12"><path d="M0 2 H12 V10 H0 Z M0.8 2.6 L6 6.5 L11.2 2.6 Z" fill-rule="evenodd"/></svg>dana.whitfield@buildmark-solutions.example</li>
        <li><svg viewBox="0 0 12 12"><path d="M6 0.5 A5 5 0 1 1 3 9.5 L0.5 11.5 L1.5 8 A5 5 0 0 1 6 0.5 Z M6 2 A3.5 3.5 0 1 0 6 9 A3.5 3.5 0 1 0 6 2 Z" fill-rule="evenodd"/></svg><span>www.<span class="contact__domain">buildmark-solutions</span>.example</span></li>
      </ul>
    </div>
  </section>

</body>
</html>
```